Veldmark Supplies Business Card

Professional business card that stand out to our potential customers. Front and back with clean modern design

Industry/Entity Type

Oil and gas

Contact Information for Business Card

Name, address, website , office phone and cell number

Requirements
Must have
• Editable files for each employee

```html
<!DOCTYPE html>
<html lang="en">
<head>
<meta charset="utf-8">
<title>Veldmark Supplies Business Card</title>
<link rel="stylesheet" href="https://fonts.googleapis.com/css2?family=Lato:wght@400;700;900&display=swap">
<style>
  :root{
    --stage:#2b2b2d;
    --card:#1b1b1c;
    --ink:#ffffff;
    --red:#ff1414;
    --blue:#19b3d6;
    --pattern-a:#0e0e0f;
    --pattern-b:#2a2a2c;
  }
  *{box-sizing:border-box;margin:0;padding:0}
  html,body{width:1200px;height:694px;overflow:hidden;background:var(--stage)}
  body{font-family:'Lato',sans-serif;color:var(--ink);position:relative}

  .card{position:absolute;top:192px;width:540px;height:310px;border-radius:22px;background:var(--card);overflow:hidden;box-shadow:0 14px 30px rgba(0,0,0,.45)}
  .card--back{left:40px}
  .card--front{left:620px}

  /* back */
  .back-pattern{position:absolute;inset:0;background:radial-gradient(ellipse at 55% 55%,var(--pattern-a) 0%,var(--pattern-b) 100%)}
  .back-brand{position:absolute;left:50%;top:50%;transform:translate(-50%,-50%);display:flex;align-items:center;gap:8px;background:var(--card);padding:8px 12px;border-radius:6px}
  .brand-square{width:16px;height:16px;background:var(--red);flex:none}
  .brand-name{font-weight:900;font-size:15px;text-transform:uppercase;letter-spacing:.04em;color:var(--ink);white-space:nowrap}

  /* front */
  .front-brand{position:absolute;right:38px;top:48px;display:flex;align-items:center;gap:10px}
  .front-brand .brand-square{width:26px;height:26px}
  .front-brand .brand-name{font-size:22px}

  .person{position:absolute;left:40px;top:112px}
  .person-name{font-size:25px;font-weight:700;color:var(--red);line-height:1}
  .person-role{font-size:15px;margin-top:8px}

  .divider{position:absolute;left:40px;right:36px;top:172px;height:1px;background:var(--ink)}

  .contacts{position:absolute;left:40px;top:186px;list-style:none}
  .contacts li,.location li{display:flex;align-items:center;gap:10px;font-size:14px;line-height:24px;white-space:nowrap}
  .icon{width:15px;height:15px;flex:none;fill:var(--blue)}

  .location{position:absolute;right:36px;top:186px;list-style:none;text-align:right}
  .location li{justify-content:flex-end}
  .location .addr{display:block;line-height:19px}

  .band{position:absolute;left:0;right:0;bottom:0;height:9px;display:flex}
  .band-red{flex:0 0 82%;background:var(--red)}
  .band-blue{flex:1;background:var(--blue)}
</style>
</head>
<body>
  <section class="card card--back">
    <div class="back-pattern" role="img" aria-label="Repeating embossed brand-mark pattern in glossy black tones"></div>
    <div class="back-brand">
      <span class="brand-square"></span>
      <span class="brand-name">Veldmark Supplies</span>
    </div>
  </section>

  <section class="card card--front">
    <div class="front-brand">
      <span class="brand-square"></span>
      <span class="brand-name">Veldmark Supplies</span>
    </div>

    <div class="person">
      <p class="person-name">Marcus Hale</p>
      <p class="person-role">Owner</p>
    </div>

    <div class="divider"></div>

    <ul class="contacts">
      <li><svg class="icon" viewBox="0 0 16 16"><path d="M3.5 1l2.5 3-1.5 1.5c.8 2 2.5 3.7 4.5 4.5L10.5 8.5l3 2.5-1.5 3C7 14 2 9 2 2.5z"/></svg>051-274 880 316</li>
      <li><svg class="icon" viewBox="0 0 16 16"><path d="M4 1h8v14H4zM5.5 2.5v9.5h5V2.5zM7.3 13h1.4v1H7.3z" fill-rule="evenodd"/></svg>072-519 630 448</li>
      <li><svg class="icon" viewBox="0 0 16 16"><path d="M1 3h14v10H1zM2 4l6 5 6-5z" fill-rule="evenodd"/></svg>info@veldmark.co</li>
    </ul>

    <ul class="location">
      <li>www.veldmarksupply.co<svg class="icon" viewBox="0 0 16 16"><circle cx="8" cy="8" r="7"/><path d="M5 4c2 0 2 2 1 3s1 3 3 2 2 3 0 4M10 2.5c0 2 2 2 3.5 2.5" stroke="#1b1b1c" stroke-width="1.2" fill="none"/></svg></li>
      <li><span><span class="addr">18 Kestrel Field Road, Unit 4</span><span class="addr">70311, Dunmore County</span></span><svg class="icon" viewBox="0 0 16 16"><path d="M8 1a5 5 0 0 1 5 5c0 4-5 9-5 9S3 10 3 6a5 5 0 0 1 5-5zm0 3a2 2 0 1 0 0 4 2 2 0 0 0 0-4z" fill-rule="evenodd"/></svg></li>
    </ul>

    <div class="band"><span class="band-red"></span><span class="band-blue"></span></div>
  </section>
</body>
</html>
```